WordPress webdesign with coding for our company BRISK The Answer

BRISK The Answer is a payrolling company such as Montaval Wages (one of our competitor https://www.montaval-wages.ch/fr/). We need to set up our website in both languages (Fr and Eng). Our logo is enclosed.
we would like something simple explaining what is payrolling in Graph and wording, who we are and a contact page. you can also take some example if needed from our mother company BRISK The Horizon (www.briskthehorizon.ch) or our sister company (www.briskyourstride.ch). we would like to keep the color panel of our logo (ref. Black = PANTONE P Process Black C
Pink = PANTONE P Process Magenta C
Grey = PANTONE 430 C) as the driver of the website.

```html
<!DOCTYPE html>
<html lang="en">
<head>
<meta charset="utf-8">
<title>BRISK The Answer – Payrolling</title>
<link href="https://fonts.googleapis.com/css2?family=Montserrat:wght@300;400;500;600;700;800&family=Rubik:wght@500;600&display=swap" rel="stylesheet">
<style>
:root{
  --pink:#ec2d8c;
  --ink:#111111;
  --text:#2b2b2b;
  --grey:#8a8d91;
  --line:#c9ccd2;
  --light:#f4f6f9;
  --white:#ffffff;
}
*{box-sizing:border-box;margin:0;padding:0}
html,body{width:1200px;height:3139px;overflow:hidden}
body{position:relative;font-family:"Montserrat",sans-serif;color:var(--text);background:var(--white)}
.abs{position:absolute}
.btn{position:absolute;background:var(--pink);color:var(--white);font-weight:700;font-size:14px;display:flex;align-items:center;justify-content:center;text-transform:uppercase;box-shadow:0 3px 6px rgba(0,0,0,.15);border-radius:2px}
/* header */
.hero-photo{left:0;top:0;width:1200px;height:760px;background:linear-gradient(90deg,#eef0f1 0%,#e4e6e8 40%,#c98a8f 62%,#b8646f 72%,#d9d4cf 90%,#ecebe8 100%)}
.hero-fade{left:0;top:0;width:700px;height:760px;background:linear-gradient(90deg,rgba(255,255,255,.85),rgba(255,255,255,0))}
.brand{left:42px;top:34px;width:210px;text-align:center;font-weight:700;color:var(--ink);line-height:1}
.brand .name{display:block;font-size:44px;letter-spacing:3px}
.brand .tag{display:block;font-size:12px;font-weight:500;letter-spacing:10px;margin-top:6px;padding-left:10px}
.nav-link{position:absolute;top:45px;font-size:13px;font-weight:500;letter-spacing:-.3px;color:var(--ink);line-height:16px;white-space:nowrap;text-decoration:none}
.nav-link.active{color:var(--pink)}
.nav-sep{position:absolute;top:44px;width:1px;height:17px;background:var(--pink)}
.lang{top:31px;left:908px;display:flex;align-items:center;gap:8px;font-size:14px;color:var(--ink)}
.flag{width:44px;height:44px;border-radius:50%;background:#1f3a8a;border:2px solid #fff;box-shadow:0 1px 3px rgba(0,0,0,.2)}
.hero-title{left:112px;top:196px;font-size:39px;font-weight:300;color:var(--ink);line-height:46px}
.hero-title strong{display:block;font-weight:800;color:var(--pink);font-size:39px;line-height:48px}
.hero-text{left:112px;top:336px;width:400px;font-size:16.5px;line-height:27.5px;color:var(--ink)}
.dots{left:112px;top:580px;display:flex;gap:6px}
.dots span{width:11px;height:11px;border-radius:50%;border:1px solid #777}
.dots span.on{background:var(--pink);border-color:var(--pink)}
/* about */
.about-photo{left:0;top:730px;width:700px;height:674px;background:linear-gradient(90deg,#6c7d90 0%,#8fa0b3 45%,rgba(230,234,240,.6) 80%,rgba(255,255,255,0) 100%)}
.sec-title{font-size:39px;font-weight:400;color:var(--ink);line-height:44px}
.sec-title b{font-weight:800;color:var(--pink)}
.rule{height:3px;width:96px;background:var(--pink)}
.body-text{font-size:16px;line-height:27px;color:var(--text)}
.body-text p+p{margin-top:10px}
.dash{left:586px;top:1526px;width:589px;height:302px;background:linear-gradient(90deg,#5b5fd6 0 80px,#f5f6fb 80px);box-shadow:0 6px 12px rgba(0,0,0,.18)}
/* contact */
.net{left:0;top:1880px;width:1200px;height:800px;background:radial-gradient(ellipse at 75% 55%,#dfe3ec 0%,#f3f5f8 55%,#ffffff 80%)}
.field{position:absolute;left:248px;width:703px;height:43px;border:1px solid #b9bec6;border-radius:6px;background:rgba(255,255,255,.85);display:flex;align-items:center;padding-left:18px;gap:12px;font-size:13.5px;color:#666}
.field svg{width:15px;height:15px;fill:var(--pink)}
.field.msg{height:124px;align-items:flex-start;padding-top:14px}
/* footer */
.foot-brand{left:129px;top:2790px;width:210px;text-align:center;color:var(--white);font-weight:700;line-height:1}
.foot-brand .name{display:block;font-size:44px;letter-spacing:3px}
.foot-brand .tag{display:block;font-size:12px;font-weight:500;letter-spacing:10px;margin-top:6px;padding-left:10px}
.foot-head{font-family:"Rubik",sans-serif;font-weight:600;font-size:20px;color:var(--white)}
.foot-rule{height:2px;width:66px;background:var(--pink);margin-top:10px}
.foot-list{list-style:none;font-size:13px;color:var(--white);line-height:26px}
.c-item{display:flex;align-items:center;gap:14px;color:var(--white)}
.c-ico{width:28px;height:28px;border-radius:50%;border:1px solid #555;display:flex;align-items:center;justify-content:center}
.c-ico svg{width:13px;height:13px;fill:var(--pink)}
.c-item small{display:block;font-size:9px;color:#ddd}
.c-item b{font-size:13px;font-weight:700}
</style>
</head>
<body>

<!-- HERO -->
<div class="abs hero-photo" role="img" aria-label="Smiling man in a pink sweater working on a laptop in a bright office"></div>
<div class="abs hero-fade"></div>
<div class="abs brand"><span class="name">BRISK</span><span class="tag">THE ANSWER</span></div>

<nav>
  <a class="nav-link active" href="#" style="left:330px">HOME</a>
  <span class="nav-sep" style="left:384px"></span>
  <a class="nav-link" href="#" style="left:399px">ABOUT US</a>
  <span class="nav-sep" style="left:481px"></span>
  <a class="nav-link" href="#" style="left:497px">WHAT IS PAYROLLING?</a>
  <span class="nav-sep" style="left:660px"></span>
  <a class="nav-link" href="#" style="left:678px">WHY CHOOSE US</a>
  <span class="nav-sep" style="left:806px"></span>
  <a class="nav-link" href="#" style="left:822px">WHY US?</a>
</nav>
<div class="abs lang"><span class="flag" role="img" aria-label="English language flag"></span><span>Eng</span>
  <svg width="10" height="7" viewBox="0 0 10 7"><path d="M1 1l4 4 4-4" stroke="#111" stroke-width="1.8" fill="none"/></svg></div>
<div class="btn" style="left:1020px;top:29px;width:160px;height:47px">Contact us</div>

<h1 class="abs hero-title">SIMPLIFYING PAYROLLING.<strong>EMPOWERING<br>YOUR WORKFORCE</strong></h1>
<p class="abs hero-text">BRISK The Answer offers transparent and efficient payrolling services for companies, freelancers, and consultants.</p>
<div class="btn" style="left:112px;top:430px;width:242px;height:45px">Discover payrolling</div>
<div class="abs dots"><span></span><span></span><span class="on"></span></div>

<!-- ABOUT -->
<div class="abs about-photo" role="img" aria-label="Team meeting around a white table in an office"></div>
<svg class="abs" style="left:0;top:620px" width="1200" height="220" viewBox="0 620 1200 220">
  <polygon points="73,633 828,760 1167,633 830,831" fill="var(--pink)"/>
</svg>

<h2 class="abs sec-title" style="left:613px;top:938px">ABOUT <b>US</b></h2>
<div class="abs rule" style="left:615px;top:997px"></div>
<div class="abs body-text" style="left:612px;top:1017px;width:490px">
  <p>Faerspiciatis unde omnis iste natus error sit voluptatem accusantium doloremque laudantium, totam rem aperiam, eaque ipsa quae ab illo inventore veritatis et quasi architecto beatae vitae dicta sunt explicabo. nesciunt. Neque porro quisquam est, qui dolorem</p>
  <p>Galoremque laudantium, totam rem aperiam, eaque ipsa quae ab illo inventore veritatis et quasi architecto beatae vitae dicta sunt explicabo. nesciunt. Neque porro quisquam est, qui dolorem</p>
</div>
<div class="btn" style="left:613px;top:1285px;width:160px;height:45px">Learn more</div>

<!-- WHAT IS PAYROLLING -->
<h2 class="abs sec-title" style="left:118px;top:1546px">WHAT IS <b>PAYROLLING</b></h2>
<div class="abs rule" style="left:118px;top:1606px"></div>
<div class="abs body-text" style="left:118px;top:1630px;width:440px">
  <p>Faerspiciatis unde omnis iste natus error sit voluptatem accusantium doloremque laudantium, totam rem aperiam, eaque ipsa quae ab illo inventore veritatis et quasi architecto beatae vitae dicta sunt explicabo. nesciunt. Neque porro quisquam est, qui dolorem</p>
</div>
<div class="btn" style="left:119px;top:1810px;width:160px;height:45px">Learn more</div>
<div class="abs dash" role="img" aria-label="Payroll dashboard with line, pie and bar charts"></div>

<!-- CONTACT -->
<div class="abs net" role="img" aria-label="Soft grey network of connected points"></div>
<h2 class="abs sec-title" style="left:0;width:1200px;text-align:center;top:1932px">CONTACT <b>US</b></h2>
<div class="abs rule" style="left:552px;top:1992px"></div>

<div class="field" style="top:2051px"><svg viewBox="0 0 16 16"><circle cx="8" cy="5" r="3.5"/><path d="M1.5 15c0-4 3-6 6.5-6s6.5 2 6.5 6z"/></svg>Your Name *</div>
<div class="field" style="top:2111px"><svg viewBox="0 0 16 16"><path d="M1 3h14v10H1z"/><path d="M1 3l7 6 7-6" stroke="#fff" stroke-width="1.4" fill="none"/></svg>Email *</div>
<div class="field" style="top:2170px"><svg viewBox="0 0 16 16"><path d="M3 1l3 3-2 2c1 2 3 4 5 5l2-2 3 3-2 3C7 15 1 9 1 3z"/></svg>Phone Number *</div>
<div class="field msg" style="top:2230px"><svg viewBox="0 0 16 16"><path d="M2 2l12 12" stroke="#ec2d8c" stroke-width="2"/></svg>Enter Your Message *</div>
<div class="btn" style="left:509px;top:2384px;width:182px;height:46px">Send message</div>

<!-- FOOTER -->
<svg class="abs" style="left:0;top:2490px" width="1200" height="649" viewBox="0 2490 1200 649">
  <polygon points="0,2719 823,2580 1200,2680 1200,3139 0,3139" fill="var(--ink)"/>
  <polygon points="73,2688 828,2496 1167,2688 823,2585" fill="var(--pink)"/>
</svg>

<div class="abs foot-brand"><span class="name">BRISK</span><span class="tag">THE ANSWER</span></div>
<div class="abs" style="left:202px;top:2899px;width:37px;height:37px;border-radius:50%;background:var(--pink)" role="img" aria-label="Professional network profile link"></div>

<div class="abs" style="left:438px;top:2763px"><div class="foot-head">Quick links</div><div class="foot-rule"></div>
  <ul class="foot-list" style="margin-top:14px"><li>Home</li><li>About Us</li><li>Services</li><li>Clients</li><li>Press</li><li>Contact Us</li></ul></div>
<div class="abs" style="left:636px;top:2763px"><div class="foot-head">Links</div><div class="foot-rule" style="width:48px"></div>
  <ul class="foot-list" style="margin-top:14px"><li>Copyright</li><li>Legal</li><li>Privacy</li><li>Accessibility</li><li>Sitemap</li></ul></div>
<div class="abs" style="left:788px;top:2763px"><div class="foot-head">Contact Us</div><div class="foot-rule" style="width:56px"></div></div>

<div class="abs c-item" style="left:788px;top:2822px"><span class="c-ico"><svg viewBox="0 0 16 16"><path d="M3 1l3 3-2 2c1 2 3 4 5 5l2-2 3 3-2 3C7 15 1 9 1 3z"/></svg></span><div><small>Call Us</small><b>+1 555 014 2290</b></div></div>
<div class="abs c-item" style="left:788px;top:2868px"><span class="c-ico"><svg viewBox="0 0 16 16"><path d="M1 3h14v10H1z"/><path d="M1 3l7 6 7-6" stroke="#111" stroke-width="1.4" fill="none"/></svg></span><div><small>Email</small><b>hello@brisk-answer.example</b></div></div>
<div class="abs c-item" style="left:788px;top:2914px"><span class="c-ico"><svg viewBox="0 0 16 16"><path d="M8 1a5 5 0 0 0-5 5c0 4 5 9 5 9s5-5 5-9a5 5 0 0 0-5-5z"/><circle cx="8" cy="6" r="2" fill="#111"/></svg></span><div><small>Address</small><b>812 Larkfield Road, Fairmont, CA 90214</b></div></div>

<div class="abs" style="left:112px;top:3006px;width:976px;height:1px;background:#333"></div>
<div class="abs" style="left:118px;top:3032px;font-size:14px;color:#fff">© 2025 .All rights reserved.</div>
<div class="abs" style="left:871px;top:3032px;font-size:14px;color:#fff">Terms of use</div>
<div class="abs" style="left:997px;top:3032px;font-size:14px;color:#fff">Privacy Policy</div>
<div class="abs" style="left:1128px;top:2989px;width:41px;height:40px;border:1px solid #fff;border-radius:8px;display:flex;align-items:center;justify-content:center">
  <svg width="12" height="8" viewBox="0 0 12 8"><path d="M1 7l5-5 5 5" stroke="#fff" stroke-width="1.6" fill="none"/></svg></div>

</body>
</html>
```